Real Estate Company / Capital Needs Cards!

need business cards designed using the logos that were just designed by pixelbarn.

Reason: per designers request deadline extended 1 day…thank you.

Target Market(s)

Investors and clients looking to purchase real estate or invest in the business.

Industry/Entity Type

Business

Requirements
Must have
• two designs - one for the real estate logo and one for the capital logo, similar but slightly different.
Nice to have
• something to make it pop (perhaps on the back)
Should not have
• much color

```html
<!DOCTYPE html>
<html lang="en">
<head>
<meta charset="utf-8">
<title>Marlow Real Estate – Business Cards</title>
<link rel="stylesheet" href="https://fonts.googleapis.com/css2?family=Source+Sans+3:wght@400;600&family=Tinos:wght@400;700&display=swap">
<style>
  :root {
    --bg: #ecebe8;
    --card: #ffffff;
    --ink: #3a3a3a;
    --grey: #7a7a7a;
    --mark: #8c8c8c;
    --rule: #9a9a9a;
    --shadow: rgba(0, 0, 0, 0.18);
  }
  * { margin: 0; padding: 0; box-sizing: border-box; }
  html, body { width: 1200px; height: 498px; overflow: hidden; background: var(--bg); }
  .canvas {
    position: relative; width: 1200px; height: 498px;
    display: flex; align-items: center; justify-content: center; gap: 60px;
  }
  .card {
    width: 520px; height: 290px; background: var(--card);
    border-radius: 26px; box-shadow: 0 6px 18px var(--shadow);
    position: relative; overflow: hidden;
  }

  /* Front */
  .card--front { display: flex; align-items: center; }
  .brand {
    display: flex; align-items: center; gap: 10px;
    font-family: "Source Sans 3", sans-serif; font-weight: 400;
    color: var(--mark); line-height: 1;
  }
  .brand__square { background: var(--mark); flex: none; }
  .brand__name { text-transform: uppercase; letter-spacing: 0.06em; }
  .brand__name span { display: block; }
  .card--front .brand { width: 215px; padding-left: 38px; }
  .card--front .brand__square { width: 38px; height: 48px; }
  .card--front .brand__name span:first-child { font-size: 30px; }
  .card--front .brand__name span:last-child { font-size: 13px; letter-spacing: 0.14em; margin-top: 3px; }

  .divider { width: 1px; height: 200px; background: var(--rule); flex: none; }

  .details { padding-left: 20px; color: var(--ink); }
  .details__name { font-family: "Tinos", serif; font-weight: 700; font-size: 17px; letter-spacing: 0.03em; }
  .details__title { font-family: "Tinos", serif; font-size: 16px; color: var(--grey); margin-bottom: 12px; }
  .contact { list-style: none; font-family: "Source Sans 3", sans-serif; }
  .contact li { display: flex; align-items: center; gap: 5px; font-size: 17px; line-height: 1.45; }
  .contact li.contact__email { font-size: 14.5px; }
  .contact svg { width: 12px; height: 12px; fill: var(--ink); flex: none; }
  .address { font-family: "Source Sans 3", sans-serif; font-size: 14.5px; line-height: 1.45; margin-top: 12px; }

  /* Back */
  .card--back { display: flex; flex-direction: column; align-items: center; justify-content: center; }
  .card--back .brand { gap: 18px; }
  .card--back .brand__square { width: 78px; height: 100px; }
  .card--back .brand__name span:first-child { font-size: 60px; }
  .card--back .brand__name span:last-child { font-size: 24px; letter-spacing: 0.14em; margin-top: 6px; }
  .website {
    margin-top: 36px; font-family: "Source Sans 3", sans-serif;
    font-size: 15px; letter-spacing: 0.2em; color: var(--ink);
  }
  .website strong { font-weight: 600; }
</style>
</head>
<body>
<main class="canvas">
  <section class="card card--front" aria-label="Business card front">
    <div class="brand">
      <span class="brand__square"></span>
      <div class="brand__name"><span>Marlow</span><span>Real Estate</span></div>
    </div>
    <div class="divider"></div>
    <div class="details">
      <p class="details__name">YOUR NAME</p>
      <p class="details__title">Title</p>
      <ul class="contact">
        <li><svg viewBox="0 0 12 12" aria-hidden="true"><path d="M2.5 1l2 2.2-1 1.2c.6 1.4 1.7 2.5 3.1 3.1l1.2-1 2.2 2-1.2 1.7C5 9.9 2 7 1 2.2z"/></svg>123-456-7980</li>
        <li><svg viewBox="0 0 12 12" aria-hidden="true"><rect x="3" y="1" width="6" height="3"/><rect x="1" y="5" width="10" height="5" rx="1"/></svg>123-568-7896</li>
        <li class="contact__email"><svg viewBox="0 0 12 12" aria-hidden="true"><path d="M1 3h10v7H1z M1.5 3.5L6 7l4.5-3.5" fill="none" stroke="#3a3a3a" stroke-width="1.2"/></svg>marlowrealestate@mail.com</li>
      </ul>
      <p class="address">Street Name, City Name<br>State ZipCode</p>
    </div>
  </section>

  <section class="card card--back" aria-label="Business card back">
    <div class="brand">
      <span class="brand__square"></span>
      <div class="brand__name"><span>Marlow</span><span>Real Estate</span></div>
    </div>
    <p class="website">www.<strong>marlowrealestate</strong>.com</p>
  </section>
</main>
</body>
</html>
```